Dunmore Roofing

Want a professional looking business card

Industry/Entity Type

Business

Contact Information for Business Card

Paul Dunmore ( Owner) paul@dunmoreroofing-example.com, www.dunmoreroofing-example.com, Adress: 4172 Township road 43 Ashcombe,ON K9X4T2

```html
<!DOCTYPE html>
<html lang="en">
<head>
<meta charset="utf-8">
<title>Dunmore Roofing – Business Card</title>
<link href="https://fonts.googleapis.com/css2?family=Roboto:wght@400;500;700&display=swap" rel="stylesheet">
<style>
  :root {
    --page-bg: #e4e4e4;
    --brand-blue: #1d4a8f;
    --brand-blue-light: #24559f;
    --card-white: #ffffff;
    --pattern-tint: #f3f5f8;
    --text-grey: #666a70;
    --divider: #d8dbe0;
    --white: #ffffff;
  }
  * { margin: 0; padding: 0; box-sizing: border-box; }
  html, body {
    width: 1200px; height: 1000px; overflow: hidden;
    background: var(--page-bg);
    font-family: "Roboto", Arial, sans-serif;
  }
  .canvas { position: relative; width: 1200px; height: 1000px; }

  .card {
    position: absolute; left: 270px; width: 660px; height: 378px;
    box-shadow: 0 3px 8px rgba(0,0,0,0.25);
    overflow: hidden;
  }
  .card--front { top: 108px; background: var(--brand-blue); }
  .card--back  { top: 521px; background: var(--card-white); }

  .card__pattern { position: absolute; inset: 0; }
  .card--front .card__pattern {
    background: linear-gradient(135deg, var(--brand-blue) 0%, var(--brand-blue-light) 100%);
  }
  .card--back .card__pattern {
    background: linear-gradient(135deg, var(--card-white) 0%, var(--pattern-tint) 100%);
  }

  .brand-name {
    position: absolute; font-weight: 700; text-transform: uppercase;
    text-align: center; white-space: nowrap;
  }
  .brand-name__mark { display: block; margin: 0 auto; }
  .brand-name__main { display: block; line-height: 1; }
  .brand-name__sub { display: block; line-height: 1; }

  .card--front .brand-name { left: 0; right: 0; top: 112px; color: var(--white); }
  .card--front .brand-name__mark { width: 72px; height: 72px; margin-bottom: 22px; background: var(--white); }
  .card--front .brand-name__main { font-size: 42px; letter-spacing: 4px; padding-left: 4px; }
  .card--front .brand-name__sub { font-size: 16px; letter-spacing: 19px; padding-left: 19px; margin-top: 10px; }

  .card--back .brand-name { left: 40px; width: 280px; top: 118px; color: var(--brand-blue); }
  .card--back .brand-name__mark { width: 60px; height: 60px; margin-bottom: 18px; background: var(--brand-blue); }
  .card--back .brand-name__main { font-size: 34px; letter-spacing: 3px; padding-left: 3px; }
  .card--back .brand-name__sub { font-size: 13px; letter-spacing: 15px; padding-left: 15px; margin-top: 8px; }

  .card__divider {
    position: absolute; left: 330px; top: 107px; width: 1px; height: 168px;
    background: var(--divider);
  }
  .contact { position: absolute; left: 355px; top: 102px; color: var(--text-grey); font-size: 15px; }
  .contact__name { color: var(--brand-blue); font-size: 19px; font-weight: 500; line-height: 24px; }
  .contact__role { font-size: 14px; line-height: 19px; }
  .contact__address { margin-top: 15px; line-height: 21px; }
  .contact__list { list-style: none; margin-top: 10px; }
  .contact__item { display: flex; align-items: center; line-height: 21px; }
  .contact__icon { width: 12px; height: 12px; margin-right: 5px; flex: none; }
  .contact__icon--fill { fill: var(--brand-blue); }
  .contact__icon--line { fill: none; stroke: var(--brand-blue); stroke-width: 2.4; }
  .contact__highlight { color: var(--brand-blue); }
</style>
</head>
<body>
<main class="canvas">
  <section class="card card--front">
    <div class="card__pattern" role="img" aria-label="Faint repeating pattern of small house roof outlines"></div>
    <div class="brand-name">
      <span class="brand-name__mark"></span>
      <span class="brand-name__main">Dunmore</span>
      <span class="brand-name__sub">Roofing</span>
    </div>
  </section>

  <section class="card card--back">
    <div class="card__pattern" role="img" aria-label="Faint repeating pattern of small house roof outlines"></div>
    <div class="brand-name">
      <span class="brand-name__mark"></span>
      <span class="brand-name__main">Dunmore</span>
      <span class="brand-name__sub">Roofing</span>
    </div>
    <div class="card__divider"></div>
    <div class="contact">
      <p class="contact__name">Paul Dunmore</p>
      <p class="contact__role">Owner</p>
      <p class="contact__address">4172 Township road 43 Ashcombe,<br>ON K9X4T2</p>
      <ul class="contact__list">
        <li class="contact__item">
          <svg class="contact__icon contact__icon--fill" viewBox="0 0 24 24"><path d="M6.6 10.8a15 15 0 0 0 6.6 6.6l2.2-2.2a1 1 0 0 1 1-.25 11.4 11.4 0 0 0 3.6.57 1 1 0 0 1 1 1V20a1 1 0 0 1-1 1A17 17 0 0 1 3 4a1 1 0 0 1 1-1h3.5a1 1 0 0 1 1 1c0 1.25.2 2.45.57 3.57a1 1 0 0 1-.25 1z"/></svg>
          (613) 555-0142
        </li>
        <li class="contact__item">
          <svg class="contact__icon contact__icon--fill" viewBox="0 0 24 24"><path d="M2 5h20v14H2z" /><path d="M2 5l10 8 10-8" fill="none" stroke="#ffffff" stroke-width="2"/></svg>
          paul@dunmoreroofing-example.com
        </li>
        <li class="contact__item">
          <svg class="contact__icon contact__icon--line" viewBox="0 0 24 24"><circle cx="12" cy="12" r="10"/><path d="M2 12h20M12 2c3 3 3 17 0 20M12 2c-3 3-3 17 0 20"/></svg>
          www.<span class="contact__highlight">dunmoreroofing-example</span>.com
        </li>
      </ul>
    </div>
  </section>
</main>
</body>
</html>
```